Private Investment Firm Needs PowerPoint Presentation Template

Design PowerPoint template, take Pinebrook-submitted rough presentation draft, and drop it into new template. See attached Project Brief file for more detail.
Updates

Some decent designs have been submitted but they seem to lack the understanding of our target markets. I am hopeful that more time and feedback will result in better results.

Target Market(s)

Private company owners and intermediaries.

Font styles to use
Serif

Colors
3176b5

Requirements
Must have
• See attached Project Brief.
Nice to have
Should not have
• No B2C fluff--this is a B2B project.

```html
<!DOCTYPE html>
<html lang="en">
<head>
<meta charset="utf-8">
<title>Pinebrook Representative Non-Control Capital Investments</title>
<link rel="stylesheet" href="https://fonts.googleapis.com/css2?family=Montserrat:wght@400;500;600;700&family=Libre+Baskerville:wght@400&display=swap">
<style>
  :root {
    --brand-blue: #0a6fc2;
    --title-blue: #1a6ac2;
    --white: #ffffff;
    --ink: #222a33;
    --mist-1: #f4f6f8;
    --mist-2: #dfe4e9;
  }
  * { box-sizing: border-box; margin: 0; padding: 0; }
  html, body { width: 1200px; height: 676px; overflow: hidden; background: var(--white); }
  .slide {
    position: relative;
    width: 1200px;
    height: 676px;
    overflow: hidden;
    background: var(--white);
    font-family: "Montserrat", Arial, sans-serif;
  }
  .side-rail {
    position: absolute; left: 0; top: 0;
    width: 44px; height: 676px;
    background: var(--brand-blue);
  }
  .side-rail__url {
    position: absolute;
    left: 22px; top: 336px;
    transform: translate(-50%, -50%) rotate(-90deg);
    white-space: nowrap;
    color: var(--white);
    font-family: "Libre Baskerville", Georgia, serif;
    font-size: 13.5px;
    letter-spacing: 0.2px;
  }
  .edge-rail {
    position: absolute; right: 0; top: 0;
    width: 12px; height: 676px;
    background: var(--brand-blue);
  }
  .page-number {
    position: absolute; right: 22px; top: 18px;
    font-family: "Libre Baskerville", Georgia, serif;
    font-size: 17px;
    color: var(--ink);
  }
  .slide-title {
    position: absolute; left: 86px; top: 82px;
    color: var(--title-blue);
    font-weight: 700;
    font-size: 28.5px;
    line-height: 33px;
    letter-spacing: 0.3px;
  }
  .architecture-backdrop {
    position: absolute; left: 470px; top: 300px;
    width: 718px; height: 376px;
    background: radial-gradient(ellipse at 80% 55%, var(--mist-2) 0%, var(--mist-1) 45%, rgba(255,255,255,0) 75%);
  }
  .case-panel {
    position: absolute; left: 45px; top: 230px;
    width: 809px; height: 352px;
    background: var(--brand-blue);
    color: var(--white);
    padding: 38px 16px 0 41px;
  }
  .case-panel__heading {
    font-weight: 600;
    font-size: 40px;
    line-height: 46px;
    letter-spacing: 0.2px;
  }
  .case-panel__list { list-style: none; margin-top: 28px; }
  .case-panel__item {
    position: relative;
    padding-left: 32px;
    font-size: 17px;
    line-height: 28px;
    margin-bottom: 28px;
    white-space: nowrap;
  }
  .case-panel__item::before {
    content: "";
    position: absolute; left: 2px; top: 9px;
    width: 10px; height: 10px;
    background: var(--white);
    opacity: 0.85;
  }
  .client-name {
    position: absolute; left: 930px; top: 558px;
    display: flex; align-items: center; gap: 10px;
    font-weight: 700;
    font-size: 40px;
    color: var(--ink);
  }
  .client-name__dot {
    width: 16px; height: 16px; border-radius: 50%;
    background: var(--ink);
  }
  .firm-mark {
    position: absolute; left: 68px; top: 616px;
    display: flex; align-items: center; gap: 10px;
    color: var(--title-blue);
    font-family: "Montserrat", Arial, sans-serif;
    font-weight: 600;
    font-size: 17px;
  }
  .firm-mark__square {
    width: 26px; height: 26px;
    background: var(--title-blue);
  }
</style>
</head>
<body>
<div class="slide">
  <div class="side-rail"><span class="side-rail__url">www.pinebrookcapital.com</span></div>
  <div class="edge-rail"></div>
  <div class="page-number">15</div>

  <h1 class="slide-title">PINEBROOK REPRESENTATIVE NON-CONTROL<br>CAPITAL INVESTMENTS</h1>

  <div class="architecture-backdrop" role="img" aria-label="Faint photograph of white modern architectural ribs"></div>

  <section class="case-panel">
    <h2 class="case-panel__heading">Balance Sheet Recapitaliza-</h2>
    <ul class="case-panel__list">
      <li class="case-panel__item">Provider of third-party vehicle maintenance services for private, public, and<br>for-hire fleet-based businesses nationwide.</li>
      <li class="case-panel__item">Pinebrook’s capital was used to support Valtrix’s accelerating growth which ex-<br>ceeded their current lender’s capacity. Pinebrook provided both subordinated debt<br>and preferred stock, altered the debt and equity mix of the business, and the<br>Company was able to grow significantly over the next three years.</li>
    </ul>
  </section>

  <div class="client-name"><span class="client-name__dot"></span>Valtrix</div>

  <div class="firm-mark">
    <span class="firm-mark__square"></span>
    <span class="firm-mark__name">Pinebrook Capital</span>
  </div>
</div>
</body>
</html>
```